Business Card and Letterhead for Pimlu - modern real estate business

I need a double sided business card design for Pimlu. Please see business card brief here https://files.trelvonadocs.com/sheet/r/7QzTmWbaXLJnoPEd-kRyUgFhHsstbvCe2qfoMxDa_pz/view?mode=shared

Please feel free to design the business cards however you feel best. I am happy to give some creative freedoms and then provide feedback from there.

Please then also create a letterhead to match the business card design

Colors

Designer to choose colors to be used in the design.

Requirements
Must have
• Must be a modern, elegant business card which looks very professional

```html
<!DOCTYPE html>
<html lang="en">
<head>
<meta charset="utf-8">
<title>Pimlu – Business Card</title>
<link href="https://fonts.googleapis.com/css2?family=Raleway:wght@300;400;500;600&display=swap" rel="stylesheet">
<style>
  :root {
    --stage: #4a4a4a;
    --card: #000000;
    --brand-red: #e0101c;
    --text-light: #f2f2f2;
    --portrait-light: #9aa3a8;
    --portrait-dark: #5b5750;
  }
  * { margin: 0; padding: 0; box-sizing: border-box; }
  html, body {
    width: 1200px; height: 890px; overflow: hidden;
    background: var(--stage);
    font-family: "Raleway", sans-serif;
  }
  .stage {
    position: relative; width: 1200px; height: 890px;
    display: flex; justify-content: center; align-items: center; gap: 40px;
  }
  .card {
    position: relative; width: 300px; height: 540px;
    background: var(--card); overflow: hidden; color: var(--text-light);
  }
  .portrait {
    position: absolute; top: 36px; left: 50%; transform: translateX(-50%);
    width: 98px; height: 114px; border-radius: 50%;
    background: linear-gradient(160deg, var(--portrait-light), var(--portrait-dark));
    border: 2px solid #ffffff;
  }
  .agent-name {
    position: absolute; top: 196px; width: 100%; text-align: center;
    font-size: 31px; font-weight: 500; letter-spacing: 0.2px;
  }
  .agent-title {
    position: absolute; top: 240px; width: 100%; text-align: center;
    font-size: 15px; font-weight: 300; color: var(--brand-red);
  }
  .contact-list {
    position: absolute; top: 326px; left: 62px; list-style: none;
  }
  .contact-list li {
    display: flex; align-items: center; gap: 22px;
    font-size: 15px; font-weight: 400; height: 34px;
  }
  .contact-list svg { width: 18px; height: 18px; fill: var(--brand-red); }
  .website {
    position: absolute; top: 436px; width: 100%;
    display: flex; flex-direction: column; align-items: center; gap: 12px;
    font-size: 15px;
  }
  .website svg { width: 20px; height: 20px; }
  .wave { position: absolute; left: 0; bottom: 0; width: 300px; height: 60px; }
  .brand-name {
    position: absolute; top: 250px; width: 100%; text-align: center;
    font-size: 38px; font-weight: 500; letter-spacing: 4px;
    color: var(--brand-red); text-transform: uppercase;
  }
  .address {
    position: absolute; top: 422px; width: 100%;
    display: flex; flex-direction: column; align-items: center;
    font-size: 15px; line-height: 21px;
  }
  .address svg { width: 18px; height: 22px; margin-bottom: 10px; fill: var(--brand-red); }
</style>
</head>
<body>
  <main class="stage">
    <section class="card card-front">
      <div class="portrait" role="img" aria-label="Portrait photo of the agent"></div>
      <h1 class="agent-name">Liam Carter</h1>
      <p class="agent-title">Licenced Real Estate Agent</p>
      <ul class="contact-list">
        <li>
          <svg viewBox="0 0 24 24" aria-hidden="true"><path d="M6.6 10.8c1.4 2.8 3.8 5.1 6.6 6.6l2.2-2.2c.3-.3.7-.4 1-.2 1.1.4 2.3.6 3.6.6.6 0 1 .4 1 1V20c0 .6-.4 1-1 1C10.6 21 3 13.4 3 4c0-.6.4-1 1-1h3.5c.6 0 1 .4 1 1 0 1.3.2 2.5.6 3.6.1.3 0 .7-.2 1l-2.3 2.2z"/></svg>
          <span>0400 318 552</span>
        </li>
        <li>
          <svg viewBox="0 0 24 24" aria-hidden="true"><path d="M20 4H4c-1.1 0-2 .9-2 2v12c0 1.1.9 2 2 2h16c1.1 0 2-.9 2-2V6c0-1.1-.9-2-2-2zm0 4-8 5-8-5V6l8 5 8-5v2z"/></svg>
          <span>liam@pimlu.com</span>
        </li>
      </ul>
      <div class="website">
        <svg viewBox="0 0 24 24" fill="none" stroke="var(--brand-red)" stroke-width="1.8" aria-hidden="true">
          <circle cx="12" cy="12" r="9"/>
          <ellipse cx="12" cy="12" rx="4" ry="9"/>
          <line x1="3" y1="12" x2="21" y2="12"/>
        </svg>
        <span>www.pimlu.com</span>
      </div>
      <svg class="wave" viewBox="0 0 300 60" preserveAspectRatio="none" aria-hidden="true">
        <path d="M0 60 L0 52 C40 30 90 14 160 22 C220 28 260 24 300 0 L300 60 Z" fill="var(--brand-red)"/>
      </svg>
    </section>

    <section class="card card-back">
      <p class="brand-name">Pimlu</p>
      <div class="address">
        <svg viewBox="0 0 24 30" aria-hidden="true"><path d="M12 1C6.5 1 2 5.4 2 10.9 2 18.3 12 29 12 29s10-10.7 10-18.1C22 5.4 17.5 1 12 1zm0 13.5a3.7 3.7 0 1 1 0-7.4 3.7 3.7 0 0 1 0 7.4z"/></svg>
        <span>PO Box 6170</span>
        <span>Larkhill NSW 2790</span>
      </div>
    </section>
  </main>
</body>
</html>
```